Newspaper ad for web design services

I have a paid space in a local newspaper size: 4.5085" W x 2.6875" H.
I want to use it for promoting my web design services.
Designers have the freedom to design the ad and the offer.
The goal is to have people contact me for business web design.
I published one ad last month and it totally failed to bring any attention.
Feel free to change or add anything you think can be more effective to attract potential customers (I can create any tripwire you consider will work)
Target: Houston-based business owners looking to get a new website or to update their existing one.

```html
<!DOCTYPE html>
<html lang="en">
<head>
<meta charset="utf-8">
<title>Harbor Pixel – Free Website E-Book Ad</title>
<link href="https://fonts.googleapis.com/css2?family=Poppins:wght@400;500;600;700;800;900&display=swap" rel="stylesheet">
<style>
  :root{
    --page-grey:#d1d2d4;
    --navy:#121229;
    --brand-blue:#4054a6;
    --accent-yellow:#f5e625;
    --white:#ffffff;
    --book-deep:#15205a;
    --book-mid:#2c4aa8;
    --book-glow:#5f86d8;
  }
  *{margin:0;padding:0;box-sizing:border-box}
  html,body{width:1200px;height:884px;overflow:hidden;background:var(--page-grey)}
  body{position:relative;font-family:"Poppins",sans-serif;color:var(--navy)}

  .ad{position:absolute;left:166px;top:183px;width:867px;height:518px;background:var(--white);overflow:hidden}
  .ad *{position:absolute;line-height:1;white-space:nowrap}

  .url-band{left:0;top:454px;width:867px;height:64px;background:var(--brand-blue)}
  .side-panel{left:24px;top:0;width:276px;height:518px;background:var(--navy)}
  .book-notch{left:160px;top:126px;width:140px;height:290px;background:var(--white)}

  .brand-square{left:43px;top:29px;width:66px;height:66px;border-radius:10px;background:var(--brand-blue)}
  .brand-name{left:122px;top:24px;color:var(--white);font-weight:500;font-size:42px;line-height:0.95;white-space:normal}

  .ebook-cover{left:90px;top:135px;width:154px;height:276px;border-radius:2px;
    background:
      radial-gradient(ellipse 60% 35% at 30% 95%, var(--book-glow) 0%, rgba(95,134,216,0) 70%),
      linear-gradient(165deg,var(--navy) 0%,var(--navy) 45%,var(--book-deep) 62%,var(--book-mid) 100%);
    box-shadow:6px 8px 14px rgba(0,0,0,.25)}

  .cta-download{left:24px;width:276px;top:431px;text-align:center;color:var(--white);font-weight:700;font-size:31px;letter-spacing:0.5px}
  .cta-free-line{left:24px;width:276px;top:465px;text-align:center;color:var(--white);font-weight:700;font-size:32px}
  .cta-free-line .free{position:static;color:var(--accent-yellow)}

  .headline{left:326px;color:var(--navy);font-weight:900;font-size:110px;letter-spacing:-4px}
  .headline.more{top:12px}
  .headline.sales{top:103px}

  .promise{left:325px;font-size:38px;font-weight:400;letter-spacing:-0.3px}
  .promise.line-1{top:236px;font-size:39px}
  .promise.line-2{top:280px;font-size:37px;letter-spacing:-0.5px}
  .promise strong{position:static;font-weight:800}
  .promise-main{left:325px;top:320px;font-size:57px;font-weight:900;letter-spacing:-1px}

  .rule{left:329px;top:391px;width:126px;height:10px;background:var(--brand-blue)}
  .tagline{left:329px;top:419px;font-size:15px;font-weight:500}

  .globe{left:334px;top:473px;width:24px;height:24px}
  .web-address{left:364px;top:466px;color:var(--white);font-weight:700;font-size:34.5px}
</style>
</head>
<body>
  <div class="ad">
    <div class="url-band"></div>
    <div class="side-panel"></div>
    <div class="book-notch"></div>

    <div class="brand-square"></div>
    <div class="brand-name">Harbor<br>Pixel</div>

    <div class="ebook-cover" role="img" aria-label="E-book cover for the website guide: title text above a rocket launching over a starry night sky"></div>

    <div class="cta-download">DOWNLOAD</div>
    <div class="cta-free-line"><span class="free">FREE</span> E-BOOK</div>

    <div class="headline more">More</div>
    <div class="headline sales">Sales?</div>

    <div class="promise line-1">The <strong>One</strong> Easy Change Will</div>
    <div class="promise line-2">Make Your Business Website</div>
    <div class="promise-main">Double Your Sale</div>

    <div class="rule"></div>
    <div class="tagline">A non-Technical Step-by-Step ACTION GUIDE for Business Owners</div>

    <svg class="globe" viewBox="0 0 24 24" aria-hidden="true">
      <circle cx="12" cy="12" r="10.5" fill="none" stroke="var(--accent-yellow)" stroke-width="2.4"/>
      <ellipse cx="12" cy="12" rx="4.5" ry="10.5" fill="none" stroke="var(--accent-yellow)" stroke-width="2.2"/>
      <line x1="1.5" y1="12" x2="22.5" y2="12" stroke="var(--accent-yellow)" stroke-width="2.2"/>
      <line x1="3.5" y1="7" x2="20.5" y2="7" stroke="var(--accent-yellow)" stroke-width="2"/>
      <line x1="3.5" y1="17" x2="20.5" y2="17" stroke="var(--accent-yellow)" stroke-width="2"/>
    </svg>
    <div class="web-address">harborpixel.com/website</div>
  </div>
</body>
</html>
```